Business Landing Page for SEO Company

Need the landing page of the website designed - I will provide the copy, will need to include details of my company and the services offered, about us, testimonials, faq, etc., and all these elements will need to be arranged graphically on the page.

I want something similar to this: https://torvanequill.com/

Not in terms of color or theme or anything, but we offer a similar service and want to display similar information.

Th services we provide are:

Premium Links
Monthly Links Subscription
Link Insertions

Need to advertise them on the front page. Additionally need a place for testimonials, company details, etc.,

We already have logo for the website. Please use the attached file to insert the logo within the overal design.

Target Market(s)

SEO marketers and agencies

Number of Pages Required

1 page

```html
<!DOCTYPE html>
<html lang="en">
<head>
<meta charset="utf-8">
<title>linkora — SEO Link Building</title>
<link href="https://fonts.googleapis.com/css2?family=Poppins:ital,wght@0,400;0,500;0,600;0,700;1,400&display=swap" rel="stylesheet">
<style>
:root{
  --blue:#2c74dd;
  --blue-dark:#1f5fc4;
  --blue-light:#a9cdf5;
  --orange:#f26a12;
  --ink:#222;
  --text:#444;
  --muted:#777;
  --faq:#ececec;
  --white:#fff;
}
*{margin:0;padding:0;box-sizing:border-box}
html,body{width:1200px;height:4222px;overflow:hidden}
body{position:relative;font-family:"Poppins",sans-serif;color:var(--text);background:var(--white)}
.abs{position:absolute}
a{color:inherit;text-decoration:none}

/* header */
.site-header{top:0;left:0;width:1200px;height:100px;background:var(--white)}
.brand{left:172px;top:22px;font-weight:700;font-size:44px;color:var(--blue);line-height:1}
.phone{left:775px;top:14px;font-weight:600;font-size:20px;color:var(--blue);display:flex;align-items:center;gap:6px}
.main-nav{left:418px;top:64px;display:flex;gap:25px;font-size:13px;font-weight:500;color:var(--ink)}
.main-nav .active{color:var(--orange)}

/* hero */
.hero{top:100px;left:0;width:1200px;height:572px;background:linear-gradient(90deg,var(--blue) 0%,#5f9bec 38%,var(--blue-light) 70%,#a3c9f4 100%);border-bottom-right-radius:110px}
.hero-welcome{left:172px;top:255px;color:var(--white);font-weight:600;font-size:30px}
.hero-brand{left:172px;top:295px;color:var(--white);font-weight:600;font-size:86px;line-height:1.1}
.hero-text{left:172px;top:420px;width:300px;color:var(--white);font-size:13px;line-height:19px}
.hero-art{left:660px;top:175px;width:500px;height:400px;border-radius:30px;background:radial-gradient(circle at 55% 50%,#e9f1fc 0%,#c4dcf7 55%,rgba(169,205,245,0) 75%)}

/* section titles */
.section-title{left:0;width:1200px;text-align:center;font-weight:700;font-size:48px;color:var(--ink)}

/* services */
.service-card{top:833px;width:258px;height:382px;background:var(--white);border-radius:10px;box-shadow:0 4px 18px rgba(0,0,0,.13);overflow:hidden}
.service-card .photo{height:172px;border-bottom-right-radius:22px}
.service-card h3{margin:20px 22px 0;color:var(--blue);font-size:21px;font-weight:700;line-height:21px}
.service-card p{margin:10px 22px 0;font-size:12.5px;line-height:18.5px;color:var(--ink)}
.service-card .more{position:absolute;left:22px;bottom:22px}

/* featured */
.featured-label{top:1322px;left:0;width:1200px;text-align:center;font-size:12px;font-weight:500;color:var(--ink)}
.featured-badge{top:1372px;width:90px;height:30px;border-radius:6px;background:#d9d9d9}

/* about */
.about-title{left:172px;top:1590px;font-size:48px;font-weight:700;color:var(--blue)}
.about-text{left:172px;top:1665px;width:360px;font-size:15px;line-height:25px;color:#555}
.btn{display:inline-block;background:var(--orange);color:var(--white);font-weight:600;font-size:14px;border-radius:24px;padding:12px 22px;text-transform:uppercase}
.about-btn{left:172px;top:1884px}
.about-art{left:533px;top:1525px;width:600px;height:400px;border-radius:40% 50% 10px 10px;background:linear-gradient(160deg,#eef3fb 0%,#d8e5f7 50%,#f3f6fb 100%)}

/* testimonials */
.testimonial{top:2168px;width:240px;text-align:center}
.testimonial .avatar{width:106px;height:106px;margin:0 auto;border-radius:50%;background:linear-gradient(150deg,#c8ccd2,#7c8088)}
.testimonial .quote{position:absolute;left:50px;top:2px;width:28px;height:28px;border-radius:50%;background:var(--blue);color:var(--white);font-size:20px;font-weight:700;line-height:34px}
.testimonial p{margin-top:22px;font-style:italic;font-size:13px;line-height:18.5px;color:var(--muted)}
.testimonial h4{margin-top:22px;color:var(--blue);font-size:13px;font-weight:600}
.testimonial .stars{color:var(--orange);font-size:11px;letter-spacing:1px}
.slider-arrow{top:2255px}

/* why choose */
.why-band{top:2651px;left:0;width:1200px;height:570px;background:var(--blue);border-top-left-radius:110px}
.why-photo{left:687px;top:2587px;width:513px;height:569px;background:linear-gradient(135deg,#6b4e36 0%,#a98a6a 40%,#d9d4cb 65%,#5c4a3a 100%)}
.why-title{left:177px;top:2792px;color:var(--white);font-weight:700;font-size:48px}
.why-text{left:177px;top:2868px;width:440px;color:var(--white);font-size:15px;line-height:25px}
.why-btn{left:177px;top:3062px}

/* faq */
.faq-intro{top:3335px;left:290px;width:620px;text-align:center;font-size:15px;line-height:22.5px;color:#555}
.faq-item{width:399px;height:62px;border-radius:31px;background:var(--faq);display:flex;align-items:center;justify-content:space-between;padding:0 10px 0 38px;font-size:16px;font-weight:500;color:var(--ink)}
.faq-item .toggle{width:36px;height:36px;border-radius:50%;background:var(--orange);display:flex;align-items:center;justify-content:center}

/* footer */
.site-footer{top:3841px;left:0;width:1200px;height:381px;background:var(--blue);border-top-right-radius:110px;color:var(--white)}
.footer-brand{left:172px;top:3910px;font-weight:700;font-size:52px;color:var(--white);line-height:1}
.socials{left:184px;top:4008px;display:flex;gap:9px}
.socials span{width:26px;height:26px;border:1.5px solid var(--white);border-radius:50%}
.footer-col{top:3901px;font-size:12.5px;line-height:19.5px}
.footer-col h5{font-size:13px;font-weight:600;text-transform:uppercase;margin-bottom:22px}
.email-field{margin-top:12px;width:162px;border-bottom:1px solid rgba(255,255,255,.6);font-style:italic;font-size:10px;padding-bottom:6px}
.signup{margin-top:22px;padding:9px 24px;font-size:12px;border:2px solid var(--white)}
.footer-rule{left:160px;top:4147px;width:880px;height:1px;background:rgba(255,255,255,.35)}
.copyright{left:0;top:4160px;width:1200px;text-align:center;font-size:12.5px}
</style>
</head>
<body>

<header class="abs site-header">
  <div class="abs brand">linkora</div>
  <a class="abs phone" href="tel:0400128764">
    <svg width="16" height="16" viewBox="0 0 24 24" fill="#2c74dd"><path d="M6.6 10.8a15.2 15.2 0 0 0 6.6 6.6l2.2-2.2c.3-.3.7-.4 1-.2 1.1.4 2.3.6 3.6.6.6 0 1 .4 1 1V20c0 .6-.4 1-1 1A17 17 0 0 1 3 4c0-.6.4-1 1-1h3.5c.6 0 1 .4 1 1 0 1.3.2 2.5.6 3.6.1.3 0 .7-.2 1z"/></svg>
    Call Us:0400128764
  </a>
  <nav class="abs main-nav">
    <a class="active">HOME</a><a>SERVICES</a><a>WHY CHOOSE</a><a>BLOG</a><a>TESTIMONIALS</a><a>ABOUT</a><a>CONTACT</a>
  </nav>
</header>

<section class="abs hero"></section>
<div class="abs hero-welcome">Welcome to</div>
<div class="abs hero-brand">linkora</div>
<p class="abs hero-text">Lorem ipsum dolor sit amet, lco ns ectetur adipiscing elit, sed do eius mod tempor incididunt ut labore et dolore magn</p>
<div class="abs hero-art" role="img" aria-label="Isometric illustration of people working with a search web page, magnifying glass and ladder"></div>

<h2 class="abs section-title" style="top:740px">Services Offered</h2>

<article class="abs service-card" style="left:172px">
  <div class="photo" role="img" aria-label="Photo of a person at a desktop showing SEO performance" style="background:linear-gradient(135deg,#e4e6ea,#8d939b)"></div>
  <h3>Premium Links</h3>
  <p>Lorem ipsum dolor sit amet, lco ns ectetur adipiscing elit, sed do eius mod tempor incididunt ut labore et dolore magna aliquat eore enima.</p>
  <svg class="more" width="26" height="10" viewBox="0 0 26 10"><path d="M0 5h24M19 1l5 4-5 4" stroke="#f26a12" stroke-width="1.5" fill="none"/></svg>
</article>
<article class="abs service-card" style="left:472px">
  <div class="photo" role="img" aria-label="Photo of hands holding a smartphone with a search bar" style="background:linear-gradient(135deg,#d8a55b,#8a7870)"></div>
  <h3>Monthly Links Subscription</h3>
  <p>Lorem ipsum dolor sit amet, lco ns ectetur adipiscing elit, sed do eius mod tempor incididunt ut labore et dolore ma</p>
  <svg class="more" width="26" height="10" viewBox="0 0 26 10"><path d="M0 5h24M19 1l5 4-5 4" stroke="#f26a12" stroke-width="1.5" fill="none"/></svg>
</article>
<article class="abs service-card" style="left:771px">
  <div class="photo" role="img" aria-label="Photo of a desk with SEO notes, glasses and coffee" style="background:linear-gradient(135deg,#5f6a3c,#a09b7e)"></div>
  <h3>Link Insertions</h3>
  <p>Lorem ipsum dolor sit amet, lco ns ectetur adipiscing elit, sed do eius mod tempor incididunt ut labore et dolore magna aliquat eore enima.</p>
  <svg class="more" width="26" height="10" viewBox="0 0 26 10"><path d="M0 5h24M19 1l5 4-5 4" stroke="#f26a12" stroke-width="1.5" fill="none"/></svg>
</article>

<div class="abs featured-label">FEATURED IN:</div>
<div class="abs featured-badge" style="left:193px"></div>
<div class="abs featured-badge" style="left:335px"></div>
<div class="abs featured-badge" style="left:476px"></div>
<div class="abs featured-badge" style="left:619px"></div>
<div class="abs featured-badge" style="left:762px"></div>
<div class="abs featured-badge" style="left:903px"></div>

<h2 class="abs about-title">About Us</h2>
<p class="abs about-text">Sed ut perspiciatis unde omnis iste natus error sit volupta tem accusantium doloremque laud antium, totamem aperiam, eaque ipsa quae ab illo inventore veritatis et quasi architecto beatae vitae dicta sunt explicabo. Nemenm psam voluptatem quia voluptas sit aspernat ur aut fgit, sed quia consequuntur magni dolores eos qui rone voluptatem</p>
<a class="abs btn about-btn">Read More</a>
<div class="abs about-art" role="img" aria-label="Illustration of a monitor with magnifying glass, phone, megaphone and envelope"></div>

<h2 class="abs section-title" style="top:2050px">Testimonials</h2>

<svg class="abs slider-arrow" style="left:82px" width="30" height="64" viewBox="0 0 30 64"><path d="M28 2L2 32l26 30" stroke="#555" stroke-width="1.5" fill="none"/></svg>
<svg class="abs slider-arrow" style="left:1070px" width="30" height="64" viewBox="0 0 30 64"><path d="M2 2l26 30L2 62" stroke="#555" stroke-width="1.5" fill="none"/></svg>

<div class="abs testimonial" style="left:169px">
  <div class="avatar" role="img" aria-label="Portrait photo of a client"></div>
  <div class="quote">“</div>
  <p>Lorem ipsum dolor sit amclo ctetur adipiscing elit, sed do eitus mod tempor incididunt ut laelot dolore magna aliquat eore egtse ddo eius mod tempor incii ut laboreet dolore maree</p>
  <h4>MILO RENWICK</h4>
  <div class="stars">★★★★★</div>
</div>
<div class="abs testimonial" style="left:480px">
  <div class="avatar" role="img" aria-label="Portrait photo of a client"></div>
  <div class="quote">“</div>
  <p>Lorem ipsum dolor sit amclo ctetur adipiscing elit, sed do eitus mod tempor incididunt ut laelot dolore magna aliquat eore egtse ddo eius mod tempor incii ut laboreet dolore maree</p>
  <h4>MILO RENWICK</h4>
  <div class="stars">★★★★★</div>
</div>
<div class="abs testimonial" style="left:790px">
  <div class="avatar" role="img" aria-label="Portrait photo of a client"></div>
  <div class="quote">“</div>
  <p>Lorem ipsum dolor sit amclo ctetur adipiscing elit, sed do eitus mod tempor incididunt ut laelot dolore magna aliquat eore egtse ddo eius mod tempor incii ut laboreet dolore maree</p>
  <h4>MILO RENWICK</h4>
  <div class="stars">★★★★★</div>
</div>

<section class="abs why-band"></section>
<div class="abs why-photo" role="img" aria-label="Overhead photo of a team reviewing printed charts and a laptop on a wooden table"></div>
<h2 class="abs why-title">Why Choose us</h2>
<p class="abs why-text">Sed ut perspiciatis unde omnis iste natus error sit volup ta tem accusantium doloremque laudantium, totamem aperiam, eaque ipsa quae ab illo inventore veritatis et qua si architecto beatae vitae dicta sunt explicabo. Nemenm psam voluptatem quia voluptas sit aspernatur aut ot t fu git, sed quia consequuntur magni dolores eos qui rone voluptatem sequi nesciuneque porrosquam.</p>
<a class="abs btn why-btn">Read More</a>

<h2 class="abs section-title" style="top:3264px">FAQ</h2>
<p class="abs faq-intro">Sed ut perspiciatis unde omnis iste natus error sit volupta tem accusantium dolor emque laud antium, totamem aperiam, eaque ipsa quae ab illo inventore verita tis et quasi architecto beatae vitae dicta sunt explicabo. Nemenm</p>

<div class="abs faq-item" style="left:189px;top:3446px">Lde omnis iste natus esit vom?<span class="toggle"><svg width="12" height="8" viewBox="0 0 12 8"><path d="M1 1l5 5 5-5" stroke="#fff" stroke-width="1.6" fill="none"/></svg></span></div>
<div class="abs faq-item" style="left:611px;top:3446px">Lde omnis iste natus esit vom?<span class="toggle"><svg width="12" height="8" viewBox="0 0 12 8"><path d="M1 1l5 5 5-5" stroke="#fff" stroke-width="1.6" fill="none"/></svg></span></div>
<div class="abs faq-item" style="left:189px;top:3521px">Lde omnis iste natus esit vom?<span class="toggle"><svg width="12" height="8" viewBox="0 0 12 8"><path d="M1 1l5 5 5-5" stroke="#fff" stroke-width="1.6" fill="none"/></svg></span></div>
<div class="abs faq-item" style="left:611px;top:3521px">Lde omnis iste natus esit vom?<span class="toggle"><svg width="12" height="8" viewBox="0 0 12 8"><path d="M1 1l5 5 5-5" stroke="#fff" stroke-width="1.6" fill="none"/></svg></span></div>
<div class="abs faq-item" style="left:189px;top:3596px">Lde omnis iste natus esit vom?<span class="toggle"><svg width="12" height="8" viewBox="0 0 12 8"><path d="M1 1l5 5 5-5" stroke="#fff" stroke-width="1.6" fill="none"/></svg></span></div>
<div class="abs faq-item" style="left:611px;top:3596px">Lde omnis iste natus esit vom?<span class="toggle"><svg width="12" height="8" viewBox="0 0 12 8"><path d="M1 1l5 5 5-5" stroke="#fff" stroke-width="1.6" fill="none"/></svg></span></div>
<div class="abs faq-item" style="left:189px;top:3672px">Lde omnis iste natus esit vom?<span class="toggle"><svg width="12" height="8" viewBox="0 0 12 8"><path d="M1 1l5 5 5-5" stroke="#fff" stroke-width="1.6" fill="none"/></svg></span></div>
<div class="abs faq-item" style="left:611px;top:3672px">Lde omnis iste natus esit vom?<span class="toggle"><svg width="12" height="8" viewBox="0 0 12 8"><path d="M1 1l5 5 5-5" stroke="#fff" stroke-width="1.6" fill="none"/></svg></span></div>

<footer class="abs site-footer"></footer>
<div class="abs footer-brand">linkora</div>
<div class="abs socials"><span></span><span></span><span></span><span></span></div>
<div class="abs footer-col" style="left:431px;width:210px;color:#fff">
  <h5>Company</h5>
  <p>Morbi pharetra blandit faucibure eros turpis, scelerisque in nisl atis blandit sem. Cras quis dui vitae puus interdum sollicitudin ut ut odiolerisquein nisi anatis blandit semas quis dui vitae puus inter dum sollictut od.</p>
</div>
<div class="abs footer-col" style="left:697px;width:190px;color:#fff">
  <h5>Newsletter</h5>
  <p>Subscribe to us to get and receive the latest news, sales and updates.</p>
  <div class="email-field">Email Address:</div>
  <a class="btn signup">Sign Up</a>
</div>
<div class="abs footer-col" style="left:934px;width:160px;color:#fff;line-height:24px">
  <h5 style="margin-bottom:16px">Links</h5>
  <p>Sed ut perspatis<br>Unde omnis inatus<br>Voluptatem ausan<br>Tium doloremque<br>Haudantium<br>Tum doloreque</p>
</div>
<div class="abs footer-rule"></div>
<div class="abs copyright" style="color:#fff">© 2021 All rights are reserved. Privacy | Terms of use</div>

</body>
</html>
```